MRT Property - Business Cards

Looking for a business card & general letterhead, signage etc design for our new logo.

Colours:
000a20
0056a2
00b5ef
0088ce
68cef2

Fonts:
Poppins
Karla

Please keep look and feel of new brand - example in the zip package I sent.

```html
<!DOCTYPE html>
<html lang="en">
<head>
<meta charset="utf-8">
<title>MRT Property – Business Cards</title>
<link rel="stylesheet" href="https://fonts.googleapis.com/css2?family=Poppins:wght@400;500;600&display=swap">
<style>
  :root {
    --ink: #000a20;
    --navy: #0056a2;
    --cyan: #00b5ef;
    --sky: #0088ce;
    --pale: #68cef2;
    --paper: #ffffff;
    --backdrop: #e9ecef;
  }
  * { margin: 0; padding: 0; box-sizing: border-box; }
  html, body { width: 900px; height: 1200px; overflow: hidden; }
  body {
    background: var(--backdrop);
    font-family: "Poppins", sans-serif;
    color: var(--ink);
    position: relative;
  }
  .card {
    position: absolute;
    width: 742px;
    height: 440px;
    border-radius: 24px;
    overflow: hidden;
  }
  .card--front { left: 80px; top: 131px; background: var(--paper); }
  .card--back { left: 79px; top: 638px; background: var(--navy); }

  .front-waves { position: absolute; inset: 0; }

  .brand-mark {
    position: absolute;
    left: 70px;
    top: 190px;
    display: flex;
    align-items: center;
    gap: 12px;
    font-weight: 600;
    font-size: 34px;
    color: var(--navy);
    white-space: nowrap;
  }
  .brand-mark__dot {
    width: 22px; height: 22px;
    border-radius: 50%;
    background: var(--cyan);
  }

  .contact-block {
    position: absolute;
    left: 348px;
    top: 97px;
    height: 224px;
    border-left: 2px solid var(--navy);
    padding-left: 16px;
  }
  .contact-block__name {
    font-size: 29px;
    font-weight: 400;
    color: var(--navy);
    line-height: 1;
    margin-top: 4px;
  }
  .contact-block__role {
    font-size: 15px;
    margin-top: 10px;
  }
  .contact-block__address {
    font-size: 15px;
    line-height: 21px;
    margin-top: 22px;
  }
  .contact-list {
    list-style: none;
    margin-top: 22px;
    font-size: 15px;
  }
  .contact-list li {
    display: flex;
    align-items: center;
    gap: 10px;
    height: 28px;
  }
  .contact-list svg { width: 16px; height: 16px; fill: var(--navy); flex: none; }

  .back-name {
    position: absolute;
    right: 72px;
    bottom: 56px;
    font-weight: 600;
    font-size: 52px;
    color: var(--paper);
    white-space: nowrap;
  }
</style>
</head>
<body>

  <section class="card card--front">
    <svg class="front-waves" viewBox="0 0 742 440" preserveAspectRatio="none" aria-hidden="true">
      <path d="M0 322 C180 300 380 390 560 392 C640 392 700 370 742 332 L742 440 L0 440 Z" fill="var(--cyan)"/>
      <path d="M0 336 C200 318 390 400 570 402 C650 402 705 384 742 354 L742 440 L0 440 Z" fill="var(--paper)"/>
      <path d="M0 346 C210 326 400 420 580 422 C660 422 710 408 742 392 L742 440 L0 440 Z" fill="var(--navy)"/>
      <path d="M420 392 C520 404 620 400 742 356 L742 368 C640 408 530 414 420 392 Z" fill="var(--pale)"/>
    </svg>

    <div class="brand-mark">
      <span class="brand-mark__dot"></span>
      <span class="brand-mark__name">MRT Property</span>
    </div>

    <div class="contact-block">
      <h1 class="contact-block__name">Daniel Hart</h1>
      <p class="contact-block__role">Mnaging Director</p>
      <p class="contact-block__address">482 Maple Ridge Ave Suite<br>210 Dayton Ohio 45402</p>
      <ul class="contact-list">
        <li>
          <svg viewBox="0 0 24 24" aria-hidden="true"><path d="M6.6 10.8a15.1 15.1 0 0 0 6.6 6.6l2.2-2.2a1 1 0 0 1 1-.25 11.4 11.4 0 0 0 3.6.57 1 1 0 0 1 1 1V20a1 1 0 0 1-1 1A17 17 0 0 1 3 4a1 1 0 0 1 1-1h3.5a1 1 0 0 1 1 1c0 1.25.2 2.45.57 3.57a1 1 0 0 1-.25 1z"/></svg>
          <span>1 (555) 014-2297</span>
        </li>
        <li>
          <svg viewBox="0 0 24 24" aria-hidden="true"><path d="M2 5h20v14H2z M2 5l10 7 10-7" fill="var(--navy)"/><path d="M3 6l9 6.3L21 6" fill="none" stroke="#fff" stroke-width="1.6"/></svg>
          <span>info@mrtproperty.com</span>
        </li>
        <li>
          <svg viewBox="0 0 24 24" aria-hidden="true"><circle cx="12" cy="12" r="10"/><path d="M2 12h20M12 2c3 3 3 17 0 20M12 2c-3 3-3 17 0 20" fill="none" stroke="#fff" stroke-width="1.4"/></svg>
          <span>www.mrtproperty.com</span>
        </li>
      </ul>
    </div>
  </section>

  <section class="card card--back">
    <p class="back-name">MRT Property</p>
  </section>

</body>
</html>
```